Luxury Candle Startup Needs Modern Packaging Box & Matching Label Design

We are Lumavale, a luxury candle company about to launch in Australia and we need a box packaging design that is modern, minimalist, and feminine. Our target audience are females, mostly mothers, within the age range of 25-45 who are looking for high quality, handmade luxurious products. Our company is going to have a large social media presence with new mothers as we are going to show our journey with starting a business whilst on maternity leave. We would like the arch shape incorporated into the box packaging as it is beautiful and symbolises moving into a new phase in life which really represents the brand. We would like for the packaging box to be a simple white box with a sleeve insert over the box with the design to make printing easier. Our colour inspiration are very earthy colours and would like the sleeve colour to be easily changed according to the scent. For example dusky rose coloured sleeve for rose patchouli and amber scent, light coffee coloured sleeve for coffee bean cacao scent etc. Please see uploaded files for inspiration, our logo, and the type of candle jars used.
The box dimensions are:
External Dimension: 95mmW x 95mmL x 116mmH
We look forward to seeing your amazing designs!

```html
<!DOCTYPE html>
<html lang="en">
<head>
<meta charset="utf-8">
<title>Lumavale – Candle Box Dieline</title>
<link rel="stylesheet" href="https://fonts.googleapis.com/css2?family=Marcellus&family=Montserrat:wght@500&family=Great+Vibes&display=swap">
<style>
  :root {
    --canvas-grey: #908f88;
    --board-white: #ffffff;
    --pattern-grey: #efefef;
    --ink-grey: #b9b9b9;
    --sleeve-rose: #dbbdb6;
    --foil-gold: #d8b46c;
  }
  html, body {
    margin: 0;
    padding: 0;
    overflow: hidden;
  }
  body {
    width: 1200px;
    height: 2283px;
    background: var(--canvas-grey);
    position: relative;
  }
  .dieline {
    position: absolute;
    left: 46px;
    top: 483px;
    width: 1107px;
    height: 1317px;
  }
  .board { fill: var(--board-white); }
  .pattern-area { fill: var(--pattern-grey); }
  .sleeve { fill: var(--sleeve-rose); }
  .foil-frame { fill: none; stroke: var(--foil-gold); stroke-width: 1.2; }
  .foil-rule { stroke: var(--foil-gold); stroke-width: 1.2; }
  .wordmark {
    font-family: "Marcellus", serif;
    font-size: 27px;
    letter-spacing: 1px;
    text-anchor: middle;
  }
  .caps {
    font-family: "Montserrat", sans-serif;
    font-weight: 500;
    text-anchor: middle;
  }
  .script {
    font-family: "Great Vibes", cursive;
    text-anchor: middle;
  }
  .ink { fill: var(--ink-grey); }
  .gold { fill: var(--foil-gold); }
</style>
</head>
<body>
<svg class="dieline" viewBox="107 1153 1107 1317" xmlns="http://www.w3.org/2000/svg">
  <!-- glue flap -->
  <path class="board" d="M174,1468 L116,1488 Q107,1492 107,1502 L107,1745 Q107,1752 116,1756 L174,1785 Z"/>

  <!-- back panel with top tuck -->
  <path class="board" d="M174,1173 Q174,1153 194,1153 L413,1153 Q433,1153 433,1173 L433,1785 L174,1785 Z"/>
  <g role="img" aria-label="Fine white-on-grey mandala ornament pattern">
    <rect class="pattern-area" x="174" y="1207" width="259" height="578"/>
  </g>
  <path class="board" d="M245,1615 L245,1545 A58.5,58.5 0 0 1 362,1545 L362,1615 Z"/>
  <rect class="board" x="174" y="1615" width="259" height="82"/>
  <rect class="board" x="245" y="1697" width="117" height="88"/>
  <text class="wordmark ink" x="303" y="1651">LUMAVALE</text>
  <text class="caps ink" x="303" y="1670" font-size="8.5" letter-spacing="2">LUXURY FRAGRANCE</text>
  <text class="caps ink" x="303" y="1684" font-size="7" letter-spacing="1.5">AUSTRALIA</text>

  <!-- left side panel with dust flaps -->
  <path class="board" d="M433,1300 Q433,1283 450,1283 L625,1283 Q633,1283 636,1292 L664,1395 L693,1432 L693,1972 L510,1972 Q498,1972 494,1960 L463,1862 L433,1825 Z"/>
  <text class="caps ink" x="565" y="1658" font-size="12" letter-spacing="4">SOY CANDLE</text>
  <text class="script ink" x="565" y="1672" font-size="15">Hand Poured</text>

  <!-- front panel with bottom tuck -->
  <path class="board" d="M693,1468 L953,1468 L953,2080 Q953,2100 933,2100 L713,2100 Q693,2100 693,2080 Z"/>
  <g role="img" aria-label="Fine white-on-grey mandala ornament pattern">
    <rect class="pattern-area" x="693" y="1468" width="260" height="147"/>
    <rect class="pattern-area" x="693" y="1697" width="260" height="88"/>
  </g>

  <!-- right side panel with dust flaps -->
  <path class="board" d="M953,1432 L982,1395 L1010,1292 Q1013,1283 1021,1283 L1214,1283 L1214,1815 Q1214,1830 1204,1840 L1184,1862 L1155,1960 Q1151,1972 1139,1972 L953,1972 Z"/>
  <text class="caps ink" x="1087" y="1655" font-size="7.5" letter-spacing="1.5">300GRAMS</text>
  <text class="caps ink" x="1087" y="1668" font-size="7.5" letter-spacing="1.5">50 HOUR BURN TIME</text>

  <!-- scent sleeve -->
  <path class="sleeve" d="M735,2470 L735,1571 A88,88 0 0 1 911,1571 L911,2470 Z"/>
  <path class="foil-frame" d="M745,1775 L745,1578 A78,78 0 0 1 901,1578 L901,1775 Z"/>
  <text class="wordmark gold" x="823" y="1662" font-size="22">LUMAVALE</text>
  <text class="caps gold" x="823" y="1677" font-size="6" letter-spacing="1.5">LUXURY FRAGRANCE</text>
  <text class="caps gold" x="823" y="1687" font-size="5" letter-spacing="1.2">AUSTRALIA</text>
  <line class="foil-rule" x1="811" y1="1705" x2="835" y2="1705"/>
  <text class="caps gold" x="823" y="1725" font-size="7" letter-spacing="1.8">ROSE PATCHOULI</text>
</svg>
</body>
</html>
```